Yearbook of one of our programs

Our company, Bluewater Circle, www.bluewatercircle.example, hosts leadership programs and workshops for women in leadership roles from different companies all around the world. We need a year book, 11 x 17 inches, we will print with a soft cover, and be approximately 70 pages. Due date for the final completion is 12/9. However, the initial contest & fee is only for pages 1-5, 26-27 and 40-41 (please see attached last year's version). We’d like to use the same color as that. Also attached is the outline we will use once a designer is selected. $50 hourly rate for the completion of the book is set once a designer is confirmed.

```html
<!DOCTYPE html>
<html lang="en">
<head>
<meta charset="utf-8">
<title>Bluewater Circle – A Year in Review 2022</title>
<link rel="stylesheet" href="https://fonts.googleapis.com/css2?family=Open+Sans:wght@400;600&family=Great+Vibes&display=swap">
<style>
  :root {
    --backdrop: #2a2624;
    --cover-light: #c43a6c;
    --cover-mid: #b32f5d;
    --cover-dark: #97284d;
    --band: #8e2744;
    --floral-deep: rgba(120, 28, 52, 0.55);
    --floral-pale: rgba(235, 170, 195, 0.35);
    --flourish-tone: rgba(255, 255, 255, 0.07);
    --ink: #ffffff;
    --ink-soft: rgba(255, 255, 255, 0.92);
  }
  * { box-sizing: border-box; margin: 0; padding: 0; }
  html, body {
    width: 1200px; height: 789px; overflow: hidden;
    background: var(--backdrop);
  }
  .canvas {
    position: relative; width: 1200px; height: 789px;
    display: flex; align-items: center; justify-content: center;
  }
  .cover {
    position: relative; width: 570px; height: 740px; overflow: hidden;
    background:
      radial-gradient(ellipse 70% 55% at 62% 40%, var(--cover-light) 0%, var(--cover-mid) 55%, var(--cover-dark) 100%);
    font-family: "Open Sans", Arial, sans-serif;
    color: var(--ink);
  }
  .floral { position: absolute; }
  .floral--top-left {
    left: -40px; top: -30px; width: 330px; height: 330px;
    background: radial-gradient(circle at 30% 30%, var(--floral-deep) 0%, rgba(120,28,52,0.25) 45%, transparent 72%);
  }
  .floral--top-right {
    right: -30px; top: -30px; width: 200px; height: 260px;
    background: radial-gradient(ellipse at 65% 35%, var(--floral-pale) 0%, rgba(235,170,195,0.12) 45%, transparent 72%);
  }
  .floral--bottom-left {
    left: -30px; bottom: -30px; width: 240px; height: 260px;
    background: radial-gradient(ellipse at 35% 65%, var(--floral-pale) 0%, rgba(235,170,195,0.12) 45%, transparent 72%);
  }
  .floral--bottom-right {
    right: -40px; bottom: -30px; width: 280px; height: 330px;
    background: radial-gradient(ellipse at 65% 65%, var(--floral-deep) 0%, rgba(120,28,52,0.25) 45%, transparent 72%);
  }
  .brand {
    position: absolute; left: 0; right: 0; top: 150px;
    display: flex; flex-direction: column; align-items: center;
  }
  .brand__dot {
    width: 72px; height: 72px; border-radius: 50%;
    border: 3px solid var(--ink);
  }
  .brand__name {
    margin-top: 26px;
    font-weight: 600; font-size: 31px; letter-spacing: 0.5px;
    line-height: 1;
  }
  .brand__tagline {
    margin-top: 6px;
    background: var(--band);
    padding: 3px 14px 4px;
    font-size: 10px; letter-spacing: 4.2px;
    color: var(--ink-soft);
  }
  .title {
    position: absolute; left: 0; right: 0; top: 380px; height: 110px;
  }
  .title__flourish {
    position: absolute; left: 150px; right: 130px; top: 0; bottom: 0;
    border-radius: 50%;
    background: radial-gradient(ellipse at center, var(--flourish-tone) 0%, transparent 70%);
  }
  .title__text {
    position: absolute; left: 0; right: 0; top: 34px;
    text-align: center;
    font-family: "Great Vibes", cursive;
    font-weight: 400;
    font-size: 40px; line-height: 1;
  }
  .edition {
    position: absolute; right: 110px; bottom: 44px;
    text-align: right;
    padding-right: 16px;
    border-right: 1.5px solid var(--ink-soft);
  }
  .edition__year { font-weight: 600; font-size: 22px; line-height: 1.1; }
  .edition__label { font-size: 16px; line-height: 1.3; color: var(--ink-soft); }
  .edition__web {
    margin-top: 8px; font-size: 11px; color: var(--ink-soft);
    display: flex; align-items: center; justify-content: flex-end; gap: 6px;
  }
</style>
</head>
<body>
<main class="canvas">
  <article class="cover">
    <div class="floral floral--top-left" role="img" aria-label="Line-drawn roses and leaves in deep rose tones"></div>
    <div class="floral floral--top-right" role="img" aria-label="Pale line-drawn rose and buds"></div>
    <div class="floral floral--bottom-left" role="img" aria-label="Pale line-drawn roses and stems"></div>
    <div class="floral floral--bottom-right" role="img" aria-label="Line-drawn rose with leaves in deep rose tones"></div>

    <header class="brand">
      <div class="brand__dot"></div>
      <h1 class="brand__name">BLUEWATER CIRCLE</h1>
      <p class="brand__tagline">LEADERSHIP · LIFE · LEGACY</p>
    </header>

    <section class="title">
      <div class="title__flourish" role="img" aria-label="Curved flourish lines framing the title"></div>
      <h2 class="title__text">A Year in Review</h2>
    </section>

    <footer class="edition">
      <p class="edition__year">2022</p>
      <p class="edition__label">Confidential</p>
      <p class="edition__web">
        <svg width="10" height="10" viewBox="0 0 10 10" aria-hidden="true"><circle cx="5" cy="5" r="4.2" fill="none" stroke="#ffffff" stroke-width="1.2"/><circle cx="5" cy="5" r="1.6" fill="#ffffff"/></svg>
        www.bluewatercircle.example
      </p>
    </footer>
  </article>
</main>
</body>
</html>
```